BPW its me again- No TIME

I am a weight loss consultant who my target audience now is staff- teachers at work.

I am Bright Path Wellness and I have partner up with the program Vital Spark Reset. I am selling my services but it will be attached to his brochure which I attached to show you.

This flyer will be given to teachers while at work or left on the staff room lunch table.

Please make it short, snappy and fun.
Why lose weight at work? People are time poor

points:-
- Mobile weight loss consultant who comes to you at work
before/after school or lunch break.
-20 minute private 1 on 1 consultations
-limited spots (3 per hour)
-no contract
-10 years experience

If possible I would like it at work flyer for different companies as well like banks but teachers/schools are my main target.

Like the picture with the teacher in front of the board but can remove the heart if possible
Thank you

i will brochure soon to show you

Target Market(s)

people at work- during lunch breaks or before and after
First is school teachers then other companies.
Females are the majority of clients

Industry/Entity Type

Teacher

Requirements
Must have
• leave it up to you just want to grab staff's attention.
Should not have
• please never use the word "diet" its a healthy lifestyle.

```html
<!DOCTYPE html>
<html lang="en">
<head>
<meta charset="utf-8">
<title>Why lose weight at work? – Bright Path Wellness</title>
<link rel="stylesheet" href="https://fonts.googleapis.com/css2?family=Open+Sans:wght@400;600;700&display=swap">
<style>
  :root {
    --red: #d4213a;
    --board: #2f4a3c;
    --board-dark: #1f3529;
    --teal: #2f6f6a;
    --paper: #f1f1f1;
    --grey: #c9c9c9;
    --purple: #4b2a78;
    --text-dark: #3a3a3a;
    --white: #ffffff;
    --stroke-green: #5fb84a;
    --stroke-purple: #8d62c7;
    --stroke-pink: #ee5a8f;
    --stroke-blue: #4ab6e6;
    --stroke-yellow: #f3cf3b;
  }
  * { margin: 0; padding: 0; box-sizing: border-box; }
  html, body { width: 851px; height: 1200px; overflow: hidden; background: var(--white); }
  body { font-family: "Open Sans", Arial, sans-serif; }
  .flyer { position: relative; width: 851px; height: 1200px; overflow: hidden; background: var(--paper); }

  .headline-bar {
    position: absolute; left: 0; top: 0; width: 851px; height: 64px;
    background: var(--white); border-bottom: 4px solid var(--red);
    display: flex; align-items: center; justify-content: center;
  }
  .headline { color: var(--red); font-size: 40px; font-weight: 600; white-space: nowrap; }

  .chalkboard {
    position: absolute; left: 0; top: 68px; width: 851px; height: 580px;
    background: radial-gradient(ellipse at 35% 40%, var(--board) 0%, var(--board-dark) 100%);
  }
  .teacher-photo {
    position: absolute; right: 0; top: 68px; width: 390px; height: 580px;
    background: linear-gradient(160deg, #7a5a48 0%, #b88f78 35%, #e6e1dc 70%, #cfc9c3 100%);
  }
  .time-banner {
    position: absolute; left: 62px; top: 108px; width: 500px; height: 70px;
    background: var(--teal); display: flex; align-items: center; padding-left: 26px;
  }
  .time-banner p { color: var(--white); font-size: 40px; font-weight: 400; white-space: nowrap; }

  .service-intro {
    position: absolute; left: 62px; top: 215px; color: var(--white);
    font-size: 29px; line-height: 1.3; white-space: nowrap;
  }
  .service-intro strong { font-weight: 400; text-transform: uppercase; }

  .diagonal { position: absolute; left: 0; top: 490px; }

  .benefits { position: absolute; left: 60px; top: 658px; list-style: none; }
  .benefits li {
    position: relative; font-size: 30px; color: var(--text-dark); height: 58px;
    line-height: 58px; padding-left: 6px; white-space: nowrap;
  }
  .benefits li span { position: relative; z-index: 1; }
  .benefits li::before {
    content: ""; position: absolute; left: -16px; top: 18px; height: 28px;
    border-radius: 14px; z-index: 0; opacity: 0.9;
  }
  .benefits .green::before { width: 200px; background: var(--stroke-green); }
  .benefits .purple::before { width: 150px; background: var(--stroke-purple); }
  .benefits .pink::before { width: 140px; background: var(--stroke-pink); }
  .benefits .blue::before { width: 170px; background: var(--stroke-blue); }
  .benefits .yellow::before { width: 160px; background: var(--stroke-yellow); }

  .brand-mark {
    position: absolute; left: 520px; top: 820px; width: 300px;
    display: flex; flex-direction: column; align-items: center; gap: 12px;
  }
  .brand-mark .dot { width: 100px; height: 100px; border-radius: 50%; background: var(--stroke-blue); }
  .brand-mark p { font-size: 30px; font-weight: 700; color: var(--purple); text-align: center; line-height: 1.15; }

  .fitness-photo {
    position: absolute; left: 28px; top: 962px; width: 170px; height: 96px;
    background: linear-gradient(120deg, #d8344a 0%, #e87a7a 40%, #9acb5a 75%, #e7e7e7 100%);
    border-radius: 6px;
  }
  .partner-badge {
    position: absolute; left: 222px; top: 976px; width: 120px; height: 68px;
    background: var(--white); border: 3px solid var(--red); border-radius: 6px;
  }

  .contact-footer {
    position: absolute; left: 0; top: 1070px; width: 851px; height: 130px;
    background: var(--purple); color: var(--white);
    display: flex; flex-direction: column; align-items: center; justify-content: center; gap: 10px;
    white-space: nowrap;
  }
  .contact-footer .line-main { font-size: 19px; }
  .contact-footer .line-social { font-size: 18px; }
</style>
</head>
<body>
<main class="flyer">
  <header class="headline-bar">
    <h1 class="headline">Why lose weight at work?</h1>
  </header>

  <section class="chalkboard"></section>
  <div class="teacher-photo" role="img" aria-label="Smiling teacher holding a green apple in front of a chalkboard"></div>

  <div class="time-banner"><p>People are time poor</p></div>

  <p class="service-intro">Mobile<br><strong>Weight loss consultant</strong><br>who comes to you at work<br>before/after school<br>or lunch break.</p>

  <svg class="diagonal" width="851" height="200" viewBox="0 0 851 200" aria-hidden="true">
    <polygon points="0,10 0,200 851,200 851,158" fill="var(--paper)"/>
    <polygon points="0,40 0,62 851,168 851,150" fill="var(--grey)"/>
  </svg>

  <ul class="benefits">
    <li class="green"><span>20 minute private 1 on 1 consultations</span></li>
    <li class="purple"><span>Limited spots (3 per hour)</span></li>
    <li class="pink"><span>No contract</span></li>
    <li class="blue"><span>10 years experience</span></li>
    <li class="yellow"><span>Convenience</span></li>
  </ul>

  <div class="brand-mark">
    <div class="dot" aria-hidden="true"></div>
    <p>Bright Path Wellness Coach</p>
  </div>

  <div class="fitness-photo" role="img" aria-label="Red dumbbells, a green apple and a measuring tape"></div>
  <div class="partner-badge" role="img" aria-label="Vital Spark Reset official partner badge"></div>

  <footer class="contact-footer">
    <p class="line-main">0400 123 456 &nbsp;|&nbsp; Maple Heights, Victoria. &nbsp;|&nbsp; hello@brightpathwellness.com.au</p>
    <p class="line-social">Visit us on brightpathwellness.com.au/community/coach-page/100200300400500</p>
  </footer>
</main>
</body>
</html>
```